Wordpress template for a mens-choire webpage

Task is to design a Wordpress template for an 98 years old estonian mens choire webpage.
Design should involve details from the attached files, choire logo and the colors of the choire flag: in horizontal orientation bright sky-blue, white, bright grass-green.
Designer signature is allowed to be added to the template, with country of origin.

Reason: Deadline extended 2 days (until 2. March 2014) to accommodate designers creativity.

Thank you everyone for your great designs!
Our project has now entered into a voting and decision phase until 14th of March 2014 (included).

```html
<!DOCTYPE html>
<html lang="en">
<head>
<meta charset="utf-8">
<title>Kuusiku Meeskoor — Estonian Mens Choire</title>
<link href="https://fonts.googleapis.com/css2?family=Ubuntu:wght@400;500&family=Open+Sans:wght@400;600&display=swap" rel="stylesheet">
<style>
:root{
  --green:#1db33f;
  --blue:#1279c8;
  --red:#b3080f;
  --red-dark:#7e0409;
  --gold:#d6a032;
  --orange:#e8a020;
  --text:#333;
  --muted:#777;
  --link-blue:#1a6fb8;
  --rule:#ddd;
}
*{margin:0;padding:0;box-sizing:border-box}
html,body{width:773px;height:1200px;overflow:hidden}
body{background:linear-gradient(180deg,var(--green) 0%,#17a37a 45%,var(--blue) 100%);font-family:'Open Sans',sans-serif;color:var(--text);position:relative}
.page{position:absolute;left:73px;top:24px;width:630px;height:1082px;background:#fff}
.abs{position:absolute}
.brand{left:20px;top:20px;display:flex;align-items:center;gap:8px;font-family:'Ubuntu',sans-serif;font-size:16px;color:var(--red);font-weight:500;width:150px;line-height:1.15}
.brand .dot{width:22px;height:22px;border-radius:50%;background:var(--red);flex:none}
.search{left:343px;top:21px;width:156px;height:16px;border:1px solid #ccc;display:flex}
.search span{flex:1;font-size:7px;color:#aaa;padding:2px 4px;white-space:nowrap}
.search b{width:41px;background:var(--orange);color:#fff;font-size:7px;font-weight:400;text-align:center;line-height:14px}
.lang{left:515px;top:20px;width:98px;height:18px;border:1px solid #bbb;font-size:7px;font-style:italic;color:#555;padding:4px 6px 0 24px}
.lang i{position:absolute;left:6px;top:5px;width:12px;height:8px;background:#2a3f8f}
.lang:after{content:"⌄";position:absolute;right:7px;top:0;font-size:9px;font-style:normal}
.phone{left:482px;top:62px;display:flex;align-items:center;gap:8px;font-family:'Ubuntu',sans-serif;font-size:17px;color:var(--orange);white-space:nowrap}
.phone .ic{width:24px;height:24px;background:#2cb34a;border-radius:4px;display:flex;align-items:center;justify-content:center}
.nav{position:absolute;left:60px;top:128px;width:655px;height:26px;background:linear-gradient(var(--red),var(--red-dark));display:flex;padding-left:168px}
.nav a{color:#fff;font-size:9px;text-decoration:none;height:26px;line-height:26px;padding:0 17px;white-space:nowrap;flex:none;border-right:1px solid rgba(0,0,0,.3)}
.nav a:last-child{border:none}
.slider{left:9px;top:138px;width:611px;height:282px;background:linear-gradient(135deg,#8a7d66,#4a3f35 45%,#2a2222 70%,#b9b2a4)}
.slider .cap{position:absolute;left:0;bottom:0;width:100%;height:34px;background:rgba(0,0,0,.45);color:#fff;font-family:'Ubuntu',sans-serif;font-size:15px;text-align:center;line-height:34px}
.slider .pager{position:absolute;right:12px;bottom:12px;display:flex;gap:5px}
.slider .pager i{width:8px;height:8px;background:#3bbf3b}
.band{font-family:'Ubuntu',sans-serif;color:#fff;font-size:14px;padding-left:18px;line-height:24px;white-space:nowrap}
.welcome{left:9px;top:446px;width:430px;height:24px;background:var(--gold);clip-path:polygon(0 0,100% 0,97% 100%,0 100%)}
.intro{left:15px;top:480px;width:424px;font-size:10px}
.body{left:15px;top:502px;width:424px;font-size:7.6px;line-height:13.6px;color:#555;text-align:justify}
.btn{left:380px;top:586px;width:60px;height:20px;background:#1766b4;color:#fff;font-size:7px;font-weight:600;text-align:center;line-height:20px}
.latest{left:9px;top:640px;width:430px;height:24px;background:var(--red);clip-path:polygon(0 0,99% 0,100% 100%,0 100%)}
.track{left:10px;width:430px;height:110px}
.track .art{position:absolute;left:0;top:0;width:106px;height:106px;border:1px solid #ddd}
.track h3{position:absolute;left:119px;top:0;font-weight:400;font-size:9.5px;color:#222;white-space:nowrap}
.track p{position:absolute;left:119px;top:18px;width:310px;font-size:7.3px;line-height:11.5px;color:#444;text-align:justify}
.track p.songs{top:60px;color:#888}
.track .price{position:absolute;left:119px;top:88px;width:155px;height:20px;border:1px solid #eee;color:var(--red);font-size:10px;text-align:center;line-height:18px}
.track .more{position:absolute;left:285px;top:88px;width:56px;height:20px;border:1px solid #eee;color:var(--red);font-size:7.5px;font-weight:600;text-align:center;line-height:18px}
.side-h{font-family:'Ubuntu',sans-serif;font-size:12px;color:#333;border-bottom:1px solid var(--rule);width:150px;padding-bottom:4px}
.shop{left:470px;width:160px;height:60px}
.shop .art{position:absolute;left:0;top:0;width:50px;height:50px}
.shop .t{position:absolute;left:59px;top:0;font-family:'Ubuntu',sans-serif;font-size:8.5px;color:#333;white-space:nowrap}
.shop .d{position:absolute;left:59px;top:14px;width:92px;font-size:7px;line-height:9px;color:#333}
.shop .m,.news .m{color:var(--red);font-size:7px;font-weight:600}
.shop .m{position:absolute;left:59px;top:45px}
.news{left:470px;width:152px;font-size:7px;line-height:11.6px;color:#333;text-align:justify}
.news .date{color:var(--link-blue)}
.social{left:73px;top:1130px;display:flex;gap:8px}
.social i{width:16px;height:16px;display:block}
.foot-links{right:71px;top:1131px;font-size:7.5px;color:#fff;text-align:right;line-height:15.5px;white-space:nowrap}
</style>
</head>
<body>
<div class="page">
  <div class="abs brand"><span class="dot"></span>Kuusiku Meeskoor</div>
  <div class="abs search"><span>type your word here</span><b>SEARCH</b></div>
  <div class="abs lang"><i></i>English</div>
  <div class="abs phone"><span class="ic"><svg width="14" height="14" viewBox="0 0 24 24"><path fill="#fff" d="M6.6 10.8a15 15 0 006.6 6.6l2.2-2.2c.3-.3.7-.4 1-.2 1.1.4 2.3.6 3.6.6.6 0 1 .4 1 1V20c0 .6-.4 1-1 1A17 17 0 013 4c0-.6.4-1 1-1h3.5c.6 0 1 .4 1 1 0 1.3.2 2.5.6 3.6.1.3 0 .7-.2 1z"/></svg></span>555-014-2783</div>

  <div class="abs slider" role="img" aria-label="Group photo of the choir in traditional costume before a stone wall">
    <div class="cap">98 Years of Estonian Choire</div>
    <div class="pager"><i></i><i></i><i></i></div>
  </div>

  <div class="abs welcome band">Welcome to Estonian Mens Choire</div>
  <div class="abs intro">Mauris vel lacus vitae felis vestibulum volutpat. Etiam est nunc, venisl.</div>
  <div class="abs body">Sed ut perspiciatis unde omnis iste natus error sit voluptatem accusantium doloremque laudantium, totam rem aperiam, eaque ipsa quae ab illo inventore veritatis et quasi architecto beatae vitae dicta sunt explicabo. Nemo enim ipsam voluptatem quia voluptas sit aspernatur aut odit aut fugit, sed quia consequuntur magni dolores eos qui ratione voluptatem sequi nesciunt. Neque porro quisquam est, qui dolorem ipsum quia dolor sit amet.Sed ut perspiciatis unde omnis iste natus error sit voluptatem accusantium doloremque.</div>
  <div class="abs btn">LEARN MORE</div>

  <div class="abs latest band">Latest Music</div>

  <div class="abs track" style="top:678px">
    <div class="art" role="img" aria-label="Vintage album cover with ornate emblem" style="background:linear-gradient(#e9d7ae,#d8bf8c)"></div>
    <h3>Maecenas vitae auctor odio. Praesent gravida nunc ornare mollis.</h3>
    <p>Nullam molestie magna leo, a vestibulum risus posuere ornare. Nunc mattis est eget nulla consectetur, eu mattis magna facilisis. Donec euismod nisl in dui commodo venenatis. Vestibulum egestas augue dui, vitae gravida nisi tincidunt quis.</p>
    <p class="songs">Songlist: Soov, Isamaa, Kuidas Elaksid?, Murdunud aer, Oolaul, Uks hetk, Kerko-kell, Jouluohtul, Ta tuli, Laulikutele, Pieta, Lapi laul, Hulkurpoiss, Uhele lapsele, Aiu-puiu,</p>
    <div class="price">8558c | 00 1 CD</div><div class="more">MORE</div>
  </div>
  <div class="abs track" style="top:814px">
    <div class="art" role="img" aria-label="Album cover with sea view framed by trees" style="background:linear-gradient(#1d2a1a,#6f8fb0 45%,#233a4a 80%,#111)"></div>
    <h3>Maecenas vitae auctor odio. Praesent gravida nunc ornare mollis.</h3>
    <p>Nullam molestie magna leo, a vestibulum risus posuere ornare. Nunc mattis est eget nulla consectetur, eu mattis magna facilisis. Donec euismod nisl in dui commodo venenatis. Vestibulum egestas augue dui, vitae gravida nisi tincidunt quis.</p>
    <p class="songs">Songlist: Soov, Isamaa, Kuidas Elaksid?, Murdunud aer, Oolaul, Uks hetk, Kerko-kell, Jouluohtul, Ta tuli, Laulikutele, Pieta, Lapi laul, Hulkurpoiss, Uhele lapsele, Aiu-puiu,</p>
    <div class="price">8558c | 00 1 CD</div><div class="more">MORE</div>
  </div>
  <div class="abs track" style="top:950px">
    <div class="art" role="img" aria-label="Album cover with dusk sky and clouds" style="background:linear-gradient(#0e1a2e,#3b4f6a 50%,#a07a4a 75%,#1a1510)"></div>
    <h3>Maecenas vitae auctor odio. Praesent gravida nunc ornare mollis.</h3>
    <p>Nullam molestie magna leo, a vestibulum risus posuere ornare. Nunc mattis est eget nulla consectetur, eu mattis magna facilisis. Donec euismod nisl in dui commodo venenatis. Vestibulum egestas augue dui, vitae gravida nisi tincidunt quis.</p>
    <p class="songs">Songlist: Soov, Isamaa, Kuidas Elaksid?, Murdunud aer, Oolaul, Uks hetk, Kerko-kell, Jouluohtul, Ta tuli, Laulikutele, Pieta, Lapi laul, Hulkurpoiss, Uhele lapsele, Aiu-puiu,</p>
    <div class="price">8558c | 00 1 CD</div><div class="more">MORE</div>
  </div>

  <div class="abs side-h" style="left:467px;top:445px">Our Music Shop</div>
  <div class="abs shop" style="top:472px"><div class="art" role="img" aria-label="Red and orange album cover" style="background:linear-gradient(var(--red),#f5a020)"></div><div class="t">Lorem Ipsum Dolor</div><div class="d">Nullam molestie magna , vestibulum ornare. Nunc mattis est eget nulla</div><div class="m">More &gt;&gt;</div></div>
  <div class="abs shop" style="top:537px"><div class="art" role="img" aria-label="Orange album cover" style="background:#f08a3a"></div><div class="t">Lorem Ipsum Dolor</div><div class="d">Nullam molestie magna , vestibulum ornare. Nunc mattis est eget nulla</div><div class="m">More &gt;&gt;</div></div>
  <div class="abs shop" style="top:602px"><div class="art" role="img" aria-label="Dark blue album cover with stars" style="background:#0d1a6a"></div><div class="t">Lorem Ipsum Dolor</div><div class="d">Nullam molestie magna , vestibulum ornare. Nunc mattis est eget nulla</div><div class="m">More &gt;&gt;</div></div>
  <div class="abs shop" style="top:667px"><div class="art" role="img" aria-label="Blue album cover with stars" style="background:#2a6aa8"></div><div class="t">Lorem Ipsum Dolor</div><div class="d">Nullam molestie magna , vestibulum ornare. Nunc mattis est eget nulla</div><div class="m">More &gt;&gt;</div></div>
  <div class="abs shop" style="top:739px"><div class="art" role="img" aria-label="Purple flower album cover" style="background:radial-gradient(circle,#c6b8f0,#5a3bb0 60%,#d8d8e8)"></div><div class="t">Lorem Ipsum Dolor</div><div class="d">Nullam molestie magna , vestibulum ornare. Nunc mattis est eget nulla</div><div class="m">More &gt;&gt;</div></div>

  <div class="abs side-h" style="left:470px;top:832px;font-size:13px">Latest <span style="color:var(--link-blue)">News</span></div>
  <div class="abs news" style="top:861px"><div class="date">Feb 14, 2014</div>Sed ut perspiciatis unde omnis iste natus voluptatem accusantium doloremque laudantium, totam aperiam.</div>
  <div class="abs news" style="top:920px"><div class="date">Feb 14, 2014</div>Sed ut perspiciatis unde omnis iste natus voluptatem accusantium doloremque laudantium, totam aperiam.</div>
  <div class="abs news" style="top:978px"><div class="date">Feb 14, 2014</div>Sed ut perspiciatis unde omnis iste natus voluptatem accusantium doloremque laudantium, totam aperiam.</div>
  <div class="abs news" style="top:1030px"><span class="m">More &gt;&gt;</span></div>
</div>
<nav class="nav"><a>Home</a><a>About Us</a><a>Services</a><a>Music</a><a>Gallery</a><a>News</a><a>Contact Us</a></nav>

<div class="abs social">
  <i style="background:#3b5998"></i><i style="background:#29b6e8"></i><i style="background:#333"></i><i style="background:#f39a1e"></i><i style="background:#d02020"></i><i style="background:#8a9aa8"></i>
</div>
<div class="abs foot-links">Privacy | Terms &nbsp;| Contactus<br>© 2014 &nbsp;estonian mens choire. All rights reserved.</div>
</body>
</html>
```